Events Company Needs Website Revamp

Tallwood Expos is an events company that specializes in organizing and marketing large scale consumer and trade events globally.

The new web design should provide easy classification of the events, and allow visitors to find and access the details page within 2 clicks.

There are no strict guidelines on the color theme. It just has to blend naturally with the corporate logo.
Updates

The company logo is uploaded (pdf & ai)

I came across this design which I like very much. Elegant and corporate with nice modern fonttype.

Layout wise, neat and clear. 

Please see how you can emulate the design further. Particularly, highlighting the 2 event arms (Trade/Consumer) clearly.

Target Market(s)

Consumer looking for upcoming events, B2C companies looking to participate, B2B companies looking to connect with other companies

Industry/Entity Type

It Company

Requirements
Must have
• The new design should help to achieve the following objectives:
1) Visitors should be able to easily identify and access the 2 different types of events (i.e. Trade Events and Consumer Events).
2) Visitors should be able to easily find events that interest them (e.g. filter by date, trade or consumer, category [i.e. beauty, retail, F&B, construction, etc.]).
3) Visitors should be able to access an event’s details page within 2 clicks from any page.

Main navigation to include the following links:
- About Us
- Calendar
- Consumer Events
- Trade Events
- Contact Us

Design for Three (3) pages required:
A. Homepage
- Clear differentiation and easy access to the 2 different types of events (trade and consumer)
- Featured area to showcase latest 4-5 events
- Quick way to access events calendar
- Clear call-to-action for newsletter signup
- Social media sharing widgets/buttons
- A section for latest news and press releases
- A section for featured testimonials

B. Events Listing Page
- List of links to all events
- Logos and/or photos of events
- Filter / tags to find events in a specific category (e.g. food, electronics, building & construction, etc.)

C. Events Details Page
- Photo strip to showcase event photos / brochure
- A section with event details (Date, Venue, Event Description, etc.)
- Call-to-action button to visit event website
- Call-to-action button to contact event sales team
- E.g. http://vantly-demo.com/user/brightfoxhk/brightfox-monday-2011 but with the photo strip permanently extended and of a shorter height. Event details and call-to-action buttons should also be easily seen

```html
<!DOCTYPE html>
<html lang="en">
<head>
<meta charset="utf-8">
<title>Tallwood Expos</title>
<link rel="stylesheet" href="https://fonts.googleapis.com/css2?family=Jost:wght@400;500&family=Open+Sans:wght@400;600;700&family=Caveat:wght@500&display=swap">
<style>
:root{
  --red:#e8163a;
  --red-dark:#b50f2c;
  --blue:#1a5aa8;
  --blue-tab:#1a56a5;
  --orange:#f9a60c;
  --pink:#d4145a;
  --ink:#1d1d1d;
  --grey:#555;
  --rule:#e3e3e3;
  --frame:#f6c89c;
  --soft:#7d95b8;
}
*{margin:0;padding:0;box-sizing:border-box}
html,body{width:991px;height:1200px;overflow:hidden;background:#fff}
body{position:relative;font-family:"Open Sans",Arial,sans-serif;color:var(--ink)}
.abs{position:absolute}
.page-edge{position:absolute;top:130px;bottom:0;width:1px;background:#e6e6e6;box-shadow:0 0 4px rgba(0,0,0,.12)}

/* header */
.brand{left:78px;top:28px;width:110px}
.brand-name{display:flex;align-items:center;gap:6px;font-family:"Jost",sans-serif;font-size:19px;font-weight:500;color:var(--ink);line-height:1}
.brand-dot{width:14px;height:14px;border-radius:50%;background:var(--orange)}
.brand-sub{margin-top:28px;font-size:6.5px;font-weight:700;color:var(--blue);letter-spacing:.2px}
.nav-item{top:44px;font-family:"Jost",sans-serif;font-size:11.5px;color:#333;letter-spacing:.2px}
.nav-rule{top:64px;height:1px;background:var(--rule)}
.submenu{top:72px;list-style:none;font-size:8.5px;line-height:16px;color:#333}
.submenu li::before{content:"";display:inline-block;width:5px;height:5px;background:var(--red);margin-right:5px;vertical-align:1px}
.tel{left:838px;top:70px;font-size:8.5px;line-height:16px;color:var(--red);font-weight:600}

/* hero */
.hero{left:65px;top:137px;width:860px;height:300px;background:var(--red);overflow:hidden}
.hero-tab{position:absolute;top:0;width:58px;border-radius:0 0 29px 29px;background:rgba(255,255,255,.06);box-shadow:2px 2px 6px rgba(0,0,0,.22)}
.hero-tab span{position:absolute;left:50%;bottom:40px;transform-origin:left bottom;transform:rotate(-90deg) translateY(50%);white-space:nowrap;font-family:"Jost",sans-serif;font-size:15px;color:rgba(255,255,255,.35)}
.hero-tab i{position:absolute;left:50%;bottom:18px;width:9px;height:9px;margin-left:-4.5px;border-radius:50%;background:rgba(255,255,255,.35)}
.hero-tab.active span{font-size:22px;color:#fff;bottom:44px}
.hero-tab.active i{width:13px;height:13px;margin-left:-6.5px;background:#fff}
.hero-copy{left:130px;top:183px;width:690px;font-family:"Jost",sans-serif;font-size:20px;line-height:25px;color:#fff}

/* section titles */
.section-title{font-family:"Jost",sans-serif;font-size:16px;color:var(--blue);font-weight:400}
.rule{height:1px;background:var(--rule)}
.filter{left:697px;top:458px;font-family:"Jost",sans-serif;font-size:12px}
.filter .consumer{color:var(--red)}
.filter .sep{color:var(--blue);margin:0 12px}
.filter .trade{color:var(--blue)}

/* featured events */
.event{width:420px;height:128px}
.event-logo{position:absolute;left:0;top:0;width:128px;height:128px;border:3px solid var(--frame)}
.event-logo.sprouts{background:linear-gradient(135deg,#2a8fd0 0%,#e9417a 60%,#f3c32b 100%)}
.event-logo.minds{background:linear-gradient(160deg,#8cc640 0%,#f47b20 55%,#2a9ad8 100%)}
.event-body{position:absolute;left:138px;top:36px;width:276px;font-size:8px;line-height:11.5px;text-align:justify;font-weight:600}
.event-body .date{color:#2a7fc0;display:block}
.event-body .more{color:var(--blue);display:block}

/* news */
.post{width:178px;font-size:8px;line-height:15.6px;text-align:justify;font-weight:600}
.post .date{color:var(--pink);display:block}
.post .more{color:var(--pink);display:block}

/* side tabs */
.side-tab{left:934px;width:31px;height:210px;color:#fff;font-family:"Jost",sans-serif;font-size:14px;letter-spacing:.5px}
.side-tab span{position:absolute;left:50%;top:50%;transform:translate(-50%,-50%) rotate(90deg);white-space:nowrap}
.side-tab.calendar{top:502px;background:var(--blue-tab)}
.side-tab.newsletter{top:768px;background:var(--orange)}

/* testimonials */
.testimonials{left:65px;top:1067px;width:860px;height:68px;background:var(--red);border-radius:7px;box-shadow:0 2px 4px rgba(0,0,0,.25)}
.testimonials h3{position:absolute;left:12px;top:12px;font-family:"Jost",sans-serif;font-weight:400;font-size:12px;color:#fff}
.testimonials svg.bubble{position:absolute;left:88px;top:8px}
.testimonials blockquote{position:absolute;left:92px;top:34px;font-size:10px;color:#fff}
.slider{position:absolute;left:633px;top:11px;width:215px;height:5px;border-radius:3px;background:var(--red-dark);box-shadow:inset 0 1px 1px rgba(0,0,0,.3)}
.slider b{position:absolute;left:87px;top:0;width:42px;height:5px;border-radius:3px;background:#fff}

/* footer */
.footer-legal{left:73px;top:1155px;font-size:7.5px;line-height:12px;color:var(--soft)}
.footer-legal .contact{color:#5a82c0}
.connect{left:725px;top:1151px;font-family:"Caveat",cursive;font-size:15px;color:#444}
.social{left:827px;top:1156px;display:flex;gap:3px}
.social i{width:15px;height:15px;border-radius:2px;background:#c9d3e0}
</style>
</head>
<body>

<div class="page-edge" style="left:57px"></div>
<div class="page-edge" style="left:933px"></div>

<!-- header -->
<div class="abs brand">
  <div class="brand-name"><span class="brand-dot"></span>Tallwood Expos</div>
  <div class="brand-sub">A SUBSIDIARY OF NORHAVEN MEDIA</div>
</div>

<nav>
  <div class="abs nav-item" style="left:241px">HOME</div>
  <div class="abs nav-item" style="left:334px">ABOUT US</div>
  <div class="abs nav-item" style="left:448px">CALENDAR</div>
  <div class="abs nav-item" style="left:563px">CONSUMER EVENTS</div>
  <div class="abs nav-item" style="left:730px">TRADE EVENTS</div>
  <div class="abs nav-item" style="left:862px">CONTACT</div>
  <div class="abs nav-rule" style="left:232px;width:66px"></div>
  <div class="abs nav-rule" style="left:318px;width:88px"></div>
  <div class="abs nav-rule" style="left:424px;width:100px"></div>
  <div class="abs nav-rule" style="left:534px;width:176px"></div>
  <div class="abs nav-rule" style="left:720px;width:108px"></div>
  <div class="abs nav-rule" style="left:840px;width:88px"></div>
  <ul class="abs submenu" style="left:323px"><li>Media Releases</li><li>Associated Companies</li><li>Gallery</li></ul>
  <ul class="abs submenu" style="left:564px"><li>Media Releases</li><li>Associated Companies</li><li>Gallery</li></ul>
  <ul class="abs submenu" style="left:728px"><li>Media Releases</li><li>Associated Companies</li><li>Gallery</li></ul>
  <div class="abs tel">Tel: (65) 6100-2840<br><span style="padding-left:15px">(65) 6100-2841</span></div>
</nav>

<!-- hero -->
<section class="abs hero">
  <div class="hero-tab active" style="left:39px;height:218px"><span>innovative</span><i></i></div>
  <div class="hero-tab" style="left:111px;height:133px"><span>entertain</span><i></i></div>
  <div class="hero-tab" style="left:183px;height:133px"><span>value-ad</span><i></i></div>
  <p class="abs hero-copy">Conceptualize events that are strongly themed and create synergy with business partners offerings.</p>
</section>

<!-- featured events -->
<h2 class="abs section-title" style="left:77px;top:454px">Featured Events</h2>
<div class="abs filter"><span class="consumer">consumer events</span><span class="sep">|</span><span class="trade">trade events</span></div>
<div class="abs rule" style="left:65px;top:478px;width:860px"></div>

<article class="abs event" style="left:71px;top:498px">
  <div class="event-logo sprouts" role="img" aria-label="Event logo for Little Sprouts Fair 2011"></div>
  <div class="event-body">Lorem ipsum dolor sit amet consec tetu eripsum dolor<span class="date">January 24, 2011 · 8 Comments</span>Lorem ipsum dolor sit amet, consec tetuer adipiscing elit. Praesent vestibulum molestie lacus. Aenean nonummyhendrerit mauris. Phasellus porta.<span class="more">Read More</span></div>
</article>
<article class="abs event" style="left:519px;top:498px">
  <div class="event-logo minds" role="img" aria-label="Event logo for Bright Minds Camp 2012 presented by Orbit Junior"></div>
  <div class="event-body">Lorem ipsum dolor sit amet consec tetu eripsum dolor<span class="date">January 24, 2011 · 8 Comments</span>Lorem ipsum dolor sit amet, consec tetuer adipiscing elit. Praesent vestibulum molestie lacus. Aenean nonummyhendrerit mauris. Phasellus porta.<span class="more">Read More</span></div>
</article>
<article class="abs event" style="left:71px;top:653px">
  <div class="event-logo sprouts" role="img" aria-label="Event logo for Little Sprouts Fair 2011"></div>
  <div class="event-body">Lorem ipsum dolor sit amet consec tetu eripsum dolor<span class="date">January 24, 2011 · 8 Comments</span>Lorem ipsum dolor sit amet, consec tetuer adipiscing elit. Praesent vestibulum molestie lacus. Aenean nonummyhendrerit mauris. Phasellus porta.<span class="more">Read More</span></div>
</article>
<article class="abs event" style="left:519px;top:653px">
  <div class="event-logo minds" role="img" aria-label="Event logo for Bright Minds Camp 2012 presented by Orbit Junior"></div>
  <div class="event-body">Lorem ipsum dolor sit amet consec tetu eripsum dolor<span class="date">January 24, 2011 · 8 Comments</span>Lorem ipsum dolor sit amet, consec tetuer adipiscing elit. Praesent vestibulum molestie lacus. Aenean nonummyhendrerit mauris. Phasellus porta.<span class="more">Read More</span></div>
</article>

<!-- news & press -->
<h2 class="abs section-title" style="left:77px;top:823px">Latest News</h2>
<h2 class="abs section-title" style="left:515px;top:823px">Press Release</h2>
<div class="abs rule" style="left:65px;top:848px;width:860px"></div>

<article class="abs post" style="left:74px;top:867px">Lorem ipsum dolor sit amet consec tetu eripsum dolor<span class="date">January 24, 2011 · 8 Comments</span>Lorem ipsum dolor sit amet, consec tetuer adipiscing elit. Praesent vestibulum molestie lacus. Aenean nonummyhendrerit mauris. Phasellus porta. Fusce suscipit varius mi. Cum sociis natoque penatibus et magnis dis parturi-ent montes, nascetur ridiculus<span class="more">Read More</span></article>
<article class="abs post" style="left:298px;top:867px">Lorem ipsum dolor sit amet consec tetu eripsum dolor<span class="date">January 24, 2011 · 8 Comments</span>Lorem ipsum dolor sit amet, consec tetuer adipiscing elit. Praesent vestibulum molestie lacus. Aenean nonummyhendrerit mauris. Phasellus porta. Fusce suscipit varius mi. Cum sociis natoque penatibus et magnis dis parturi-ent montes, nascetur ridiculus<span class="more">Read More</span></article>
<article class="abs post" style="left:515px;top:867px">Lorem ipsum dolor sit amet consec tetu eripsum dolor<span class="date">January 24, 2011 · 8 Comments</span>Lorem ipsum dolor sit amet, consec tetuer adipiscing elit. Praesent vestibulum molestie lacus. Aenean nonummyhendrerit mauris. Phasellus porta. Fusce suscipit varius mi. Cum sociis natoque penatibus et magnis dis parturi-ent montes, nascetur ridiculus<span class="more">Read More</span></article>
<article class="abs post" style="left:726px;top:867px">Lorem ipsum dolor sit amet consec tetu eripsum dolor<span class="date">January 24, 2011 · 8 Comments</span>Lorem ipsum dolor sit amet, consec tetuer adipiscing elit. Praesent vestibulum molestie lacus. Aenean nonummyhendrerit mauris. Phasellus porta. Fusce suscipit varius mi. Cum sociis natoque penatibus et magnis dis parturi-ent montes, nascetur ridiculus<span class="more">Read More</span></article>

<!-- side tabs -->
<a class="abs side-tab calendar"><span>view our calendar</span></a>
<a class="abs side-tab newsletter"><span>newsletter sign up</span></a>

<!-- testimonials -->
<section class="abs testimonials">
  <h3>Testimonials</h3>
  <svg class="bubble" width="26" height="20" viewBox="0 0 26 20" aria-hidden="true">
    <path d="M4 10 C1 10 1 4 5 4 C6 0 13 0 14 3 C17 1 22 2 22 6 C26 7 25 13 21 13 L12 13 L8 18 L8 13 C6 13 4 12 4 10 Z" fill="#fff"/>
  </svg>
  <div class="slider"><b></b></div>
  <blockquote>“Aenean nonummy hendrerit mauris. Phasellus porta. Fusce suscipit varius mi. Cum sociis natoqu suscipit varius.”- Marla</blockquote>
</section>

<!-- footer -->
<footer>
  <div class="abs footer-legal">Copyright © Tallwood Expos 2008-2010. All Rights Reserved.<br><span class="contact">Tel: (65) 6100-2840 or (65) 6100-2841 &nbsp;•&nbsp; Fax: (65) 6100-2960 &nbsp;•&nbsp; hello@tallwoodexpos.example</span></div>
  <div class="abs connect">connect with us</div>
  <div class="abs social" aria-label="Social links"><i></i><i></i><i></i><i></i><i></i></div>
</footer>

</body>
</html>
```